KRT Project Signage

Need a sign to be displayed in the front of properties currently under Construction or Renovation to advertise our company information. Need it to be Professional and Contemporary. We are a Design/Build Construction Company. Information should include Company Name, email, website, phone number. Attached: Logo and company brochure, also included and inspiration images

```html
<!DOCTYPE html>
<html lang="en">
<head>
<meta charset="UTF-8">
<title>KRT Project Sign</title>
<link rel="stylesheet" href="https://fonts.googleapis.com/css2?family=Jost:wght@500;700&family=Poppins:wght@400;500;700&display=swap">
<style>
  :root {
    --sign-yellow: #f2ec45;
    --sign-olive: #a99b11;
    --sign-black: #000000;
    --sign-white: #ffffff;
    --page-bg: #ffffff;
  }
  html, body {
    margin: 0;
    padding: 0;
    width: 686px;
    height: 1200px;
    overflow: hidden;
    background: var(--page-bg);
  }
  .project-sign {
    display: block;
    width: 686px;
    height: 1200px;
  }
  .name-first { font-family: "Jost", sans-serif; font-weight: 700; fill: var(--sign-black); }
  .name-last { font-family: "Jost", sans-serif; font-weight: 500; fill: var(--sign-black); }
  .tagline { font-family: "Poppins", sans-serif; font-weight: 500; fill: var(--sign-yellow); letter-spacing: 0.5px; }
  .contact-line { font-family: "Poppins", sans-serif; font-weight: 400; fill: var(--sign-white); }
  .phone-number { font-family: "Poppins", sans-serif; font-weight: 700; fill: var(--sign-black); }
  .company-name { font-family: "Poppins", sans-serif; font-weight: 500; fill: var(--sign-black); letter-spacing: 1px; }
</style>
</head>
<body>
<svg class="project-sign" viewBox="0 0 686 1200" xmlns="http://www.w3.org/2000/svg" aria-label="KRT project sign">
  <defs>
    <clipPath id="inner-disc">
      <circle cx="343" cy="222" r="233"/>
    </clipPath>
  </defs>

  <!-- background panels -->
  <rect class="panel-white" x="0" y="0" width="686" height="1200" fill="var(--sign-white)"/>
  <path class="panel-black" d="M0 227 Q343 110 686 222 L686 840 L0 840 Z" fill="var(--sign-black)"/>
  <path class="band-yellow" d="M0 832 Q343 730 686 832 L686 985 L0 985 Z" fill="var(--sign-yellow)"/>

  <!-- emblem rings -->
  <g class="emblem">
    <circle cx="343" cy="222" r="315" fill="var(--sign-yellow)"/>
    <circle cx="343" cy="222" r="288" fill="var(--sign-white)"/>
    <circle cx="343" cy="222" r="264" fill="var(--sign-yellow)"/>
    <circle cx="343" cy="222" r="233" fill="var(--sign-white)"/>
    <path class="emblem-olive" clip-path="url(#inner-disc)" d="M0 300 Q343 262 686 278 L686 500 L0 500 Z" fill="var(--sign-olive)"/>
  </g>

  <!-- guide lines -->
  <rect class="guide-top" x="338" y="0" width="10" height="64" fill="var(--sign-yellow)"/>
  <rect class="guide-center" x="336" y="368" width="14" height="168" rx="3" fill="var(--sign-white)"/>
  <rect class="guide-center-core" x="339" y="370" width="8" height="166" rx="2" fill="var(--sign-yellow)"/>

  <!-- name -->
  <text class="name-first" x="343" y="166" font-size="104" text-anchor="middle" textLength="358" lengthAdjust="spacingAndGlyphs">DAMIAN</text>
  <text class="name-last" x="343" y="276" font-size="112" text-anchor="middle" textLength="322" lengthAdjust="spacingAndGlyphs">HOLTER</text>
  <text class="tagline" x="343" y="350" font-size="30" text-anchor="middle">DESIGN &amp; BUILDER</text>

  <!-- location & mail icons -->
  <g class="icon-location">
    <circle cx="313" cy="545" r="24" fill="var(--sign-yellow)" stroke="var(--sign-black)" stroke-width="2"/>
    <path d="M313 531 a9 9 0 0 1 9 9 c0 7 -9 17 -9 17 c0 0 -9 -10 -9 -17 a9 9 0 0 1 9 -9 Z" fill="var(--sign-black)"/>
    <circle cx="313" cy="540" r="3.2" fill="var(--sign-yellow)"/>
  </g>
  <g class="icon-mail">
    <circle cx="374" cy="545" r="24" fill="var(--sign-yellow)" stroke="var(--sign-black)" stroke-width="2"/>
    <rect x="360" y="536" width="28" height="19" rx="1.5" fill="none" stroke="var(--sign-black)" stroke-width="2.4"/>
    <path d="M360 537 L374 548 L388 537" fill="none" stroke="var(--sign-black)" stroke-width="2.4"/>
  </g>

  <!-- contact details -->
  <text class="contact-line" x="343" y="620" font-size="27" text-anchor="middle">1480 Harbor View Rd., Ste. 310</text>
  <text class="contact-line" x="343" y="661" font-size="27" text-anchor="middle">Coral Bay, FL 33410</text>
  <text class="contact-line" x="343" y="722" font-size="29" text-anchor="middle">info@krtconstruction.com</text>

  <!-- phone & fax icons -->
  <g class="icon-phone">
    <circle cx="310" cy="824" r="25" fill="var(--sign-black)" stroke="var(--sign-yellow)" stroke-width="2"/>
    <path d="M301 812 l6 -2 l4 9 l-4 3 c2 5 5 8 10 10 l3 -4 l9 4 l-2 6 c-14 1 -27 -12 -26 -26 Z" fill="var(--sign-white)"/>
  </g>
  <g class="icon-fax">
    <circle cx="379" cy="824" r="25" fill="var(--sign-black)" stroke="var(--sign-yellow)" stroke-width="2"/>
    <rect x="366" y="816" width="6" height="20" rx="1" fill="var(--sign-white)"/>
    <rect x="374" y="818" width="18" height="18" rx="1.5" fill="var(--sign-white)"/>
    <rect x="377" y="810" width="12" height="8" fill="var(--sign-white)"/>
    <g fill="var(--sign-black)">
      <rect x="377" y="822" width="3" height="3"/><rect x="382" y="822" width="3" height="3"/><rect x="387" y="822" width="3" height="3"/>
      <rect x="377" y="828" width="3" height="3"/><rect x="382" y="828" width="3" height="3"/><rect x="387" y="828" width="3" height="3"/>
    </g>
  </g>

  <!-- phone box -->
  <rect class="phone-box" x="40" y="851" width="605" height="108" rx="10" fill="none" stroke="var(--sign-black)" stroke-width="1.2"/>
  <text class="phone-number" x="66" y="928" font-size="42" textLength="268" lengthAdjust="spacingAndGlyphs">555-214-7788</text>
  <rect class="phone-divider" x="343" y="890" width="1.5" height="44" fill="var(--sign-black)"/>
  <text class="phone-number" x="353" y="928" font-size="42" textLength="267" lengthAdjust="spacingAndGlyphs">555.306.4129</text>

  <!-- company name -->
  <circle class="company-dot" cx="180" cy="1058" r="12" fill="var(--sign-yellow)"/>
  <text class="company-name" x="203" y="1068" font-size="27">KRT CONSTRUCTION</text>
</svg>
</body>
</html>
```